Business card for law firm

Need business card for new law firm. Think confident, authoritative, conservative, but not stuffy or old-fashioned.

Contact Information for Business Card

Content for card - logo (uploaded), plus the following:

Paul Whitcombe (larger font)
Managing Partner (larger font, but not as large as name)
Level 9, 7 Ferris Lane
Sydney NSW 2000
Main Tel 02 9364 2710
Direct Tel 02 8472 3159
Email paul@qvlegal.com.au
www.qvlegal.com.au

Letterhead design should include logo plus:
Level 9, 7 Ferris Lane
Sydney NSW 2000
Tel 02 8472 3159
www.qvlegal.com.au

```html
<!DOCTYPE html>
<html lang="en">
<head>
<meta charset="utf-8">
<title>Quayvale Legal — Letterhead</title>
<link rel="stylesheet" href="https://fonts.googleapis.com/css2?family=Open+Sans:wght@400;600&family=Lato:wght@400&display=swap">
<style>
  :root {
    --navy: #0d1f5c;
    --ink: #3a3a3a;
    --ink-dark: #1b1b1b;
    --paper: #ffffff;
  }
  * { box-sizing: border-box; margin: 0; padding: 0; }
  html, body { width: 1040px; height: 1200px; overflow: hidden; background: var(--paper); }
  .letterhead {
    position: relative;
    width: 1040px;
    height: 1200px;
    background: var(--paper);
    font-family: "Open Sans", sans-serif;
    color: var(--ink);
  }
  .edge-band {
    position: absolute; left: 0; top: 0;
    width: 16px; height: 100%;
    background: var(--navy);
  }
  .brand {
    position: absolute; top: 40px; left: 16px; right: 0;
    display: flex; flex-direction: column; align-items: center; gap: 40px;
  }
  .brand-square { width: 66px; height: 66px; background: var(--navy); }
  .brand-name {
    font-family: "Open Sans", sans-serif;
    font-weight: 600;
    font-size: 31px;
    line-height: 36px;
    letter-spacing: 3px;
    color: var(--navy);
  }
  .content {
    position: absolute; left: 99px; width: 840px;
    font-size: 16px;
  }
  .issue-date { top: 214px; }
  .recipient { top: 252px; line-height: 19px; font-style: normal; }
  .salutation { top: 355px; }
  .body { top: 407px; }
  .body p {
    line-height: 27px;
    text-align: justify;
    hyphens: auto;
    margin-bottom: 27px;
  }
  .closing { top: 813px; }
  .signatory { top: 890px; }
  .signatory-name { font-size: 19px; color: var(--ink-dark); }
  .signatory-role { font-size: 15px; margin-top: 5px; }
  .contact-bar {
    position: absolute; left: 16px; right: 0; top: 1148px;
    display: flex; justify-content: center; gap: 42px;
    font-family: "Lato", sans-serif;
    font-size: 19px; color: var(--ink-dark);
  }
  .contact-item { display: flex; align-items: center; gap: 8px; }
  .contact-icon { width: 21px; height: 21px; flex: none; }
</style>
</head>
<body>
<main class="letterhead">
  <div class="edge-band"></div>

  <header class="brand">
    <div class="brand-square"></div>
    <div class="brand-name">QUAYVALE LEGAL</div>
  </header>

  <p class="content issue-date">Issuing Date: May 5, 2018</p>

  <address class="content recipient">
    Name Of Employee Mr. XYZABC<br>
    Address of Employee<br>
    Address Line 2 etc..
  </address>

  <p class="content salutation">Dear Mr.XYZABC</p>

  <section class="content body">
    <p>Lorem Ipsum has been the industry's standard dummy text ever since the 1500s, when an unknown printer took a galley of type and scrambled it to make a type specimen book. It has survived not only five centuries, but also the leap into electronic typesetting, remaining essentially unchanged. It was popularised in the 1960s with the release of Linotrace sheets containing Lorem Ipsum passages, and more recently with desktop publishing software like Folio PageSmith including versions of Lorem Ipsum.</p>
    <p>Lorem Ipsum is simply dummy text of the printing and typesetting industry. Lorem Ipsum has been the industry's standard dummy text ever since the 1500s, when an unknown printer took a galley of type and scrambled it to make a type specimen book.</p>
    <p>It has survived not only five centuries, but also the leap into electronic typesetting, remaining essentially unchanged. It was popularised in the 1960s with the release of Linotrace sheets containing Lorem IpsumIpsum passages.</p>
  </section>

  <p class="content closing">Yours Sincerely</p>

  <div class="content signatory">
    <p class="signatory-name">Daniel Ashford</p>
    <p class="signatory-role">Managing Director</p>
  </div>

  <footer class="contact-bar">
    <span class="contact-item">
      <svg class="contact-icon" viewBox="0 0 20 20" aria-hidden="true">
        <rect width="20" height="20" rx="4" fill="#0d1f5c"/>
        <path d="M6.2 4.5l2 .2.8 2.8-1.4 1.1a7 7 0 0 0 3.8 3.8l1.1-1.4 2.8.8.2 2c-.1.7-.7 1.2-1.4 1.2A10 10 0 0 1 5 6c0-.7.5-1.3 1.2-1.5z" fill="#fff"/>
      </svg>
      02 8472 3159
    </span>
    <span class="contact-item">
      <svg class="contact-icon" viewBox="0 0 20 20" aria-hidden="true">
        <rect width="20" height="20" rx="4" fill="#0d1f5c"/>
        <circle cx="10" cy="10" r="5.5" fill="none" stroke="#fff" stroke-width="1.6"/>
        <path d="M4.5 10h11M10 4.5c-2.4 3-2.4 8 0 11M10 4.5c2.4 3 2.4 8 0 11" fill="none" stroke="#fff" stroke-width="1.2"/>
      </svg>
      www.qvlegal.com.au
    </span>
    <span class="contact-item">
      <svg class="contact-icon" viewBox="0 0 20 20" aria-hidden="true">
        <rect width="20" height="20" rx="4" fill="#0d1f5c"/>
        <path d="M10 3.8a4.4 4.4 0 0 0-4.4 4.4c0 3.3 4.4 8 4.4 8s4.4-4.7 4.4-8A4.4 4.4 0 0 0 10 3.8z" fill="#fff"/>
        <circle cx="10" cy="8.2" r="1.7" fill="#0d1f5c"/>
      </svg>
      Level 9, 7 Ferris Lane Sydney NSW 2000
    </span>
  </footer>
</main>
</body>
</html>
```